Construction material supplies company business card ****

1. Full company name “K T Masonry Works Ltd”
I am after a Business card design for the company as a whole. We are better known in Solomon Islands as “K T Masonry” for short.

We are a building materials supplier of
Ready Mixed Concrete, Bricks and Blocks,
Quarry products- gravel, aggregates, sand etc.
Cement distributor/retailer of reputable brands.
Other prefab concrete products. Culverts, wave breakers, concrete retaining blocks etc.

2. Competitive Advantage over Competition: Quality, efficient, professional, dependable, reliable

3. We want people to feel trust worthy, high quality, strong when they see our brand

5. No preference to color. Maybe more sturdy and corporate. Not fancy.

Industry/Entity Type

CONSTRUCTION SUPPLY

Contact Information for Business Card

Name, Position, office phone mob phone, email

Requirements
Must have
• the company logo
Nice to have
• would like to see a mixture of designs, of with logo only and also with simple graphic designs to bring out the company whilst still have the strong sturdy professional feeling

```html
<!DOCTYPE html>
<html lang="en">
<head>
<meta charset="utf-8">
<title>K T Masonry – Business Card</title>
<link rel="stylesheet" href="https://fonts.googleapis.com/css2?family=Roboto:wght@400;500;700&display=swap">
<style>
  :root {
    --backdrop: #2c2c2c;
    --card-light: #ececec;
    --card-mid: #dcdcdc;
    --ink: #163a5c;
    --mark-faint: #c9c9c9;
  }
  * { margin: 0; padding: 0; box-sizing: border-box; }
  html, body {
    width: 1200px;
    height: 1138px;
    overflow: hidden;
    background: var(--backdrop);
    font-family: "Roboto", Arial, sans-serif;
    color: var(--ink);
  }
  .canvas {
    position: relative;
    width: 1200px;
    height: 1138px;
  }
  .card {
    position: absolute;
    left: 275px;
    width: 620px;
    height: 374px;
    border-radius: 16px;
    background: radial-gradient(ellipse at 50% 40%, var(--card-light) 0%, var(--card-mid) 100%);
    overflow: hidden;
  }
  .card--front { top: 186px; }
  .card--back  { top: 608px; }

  /* Front */
  .front__name {
    position: absolute;
    left: 0; right: 0;
    top: 160px;
    text-align: center;
    font-size: 48px;
    font-weight: 700;
    letter-spacing: 2px;
    color: var(--mark-faint);
    text-transform: uppercase;
  }
  .front__web {
    position: absolute;
    left: 0; right: 0;
    top: 333px;
    text-align: center;
    font-size: 14px;
    font-weight: 500;
    letter-spacing: 6.5px;
    color: var(--ink);
  }

  /* Back */
  .brand {
    position: absolute;
    left: 40px;
    top: 180px;
    width: 236px;
    text-align: center;
    display: flex;
    flex-direction: column;
    align-items: center;
    gap: 16px;
  }
  .brand__square {
    width: 58px;
    height: 58px;
    background: var(--ink);
  }
  .brand__name {
    font-size: 29px;
    font-weight: 700;
    letter-spacing: 1px;
    color: var(--ink);
    text-transform: uppercase;
    white-space: nowrap;
  }
  .contact {
    position: absolute;
    left: 344px;
    top: 80px;
  }
  .contact__name {
    font-size: 23px;
    font-weight: 700;
    line-height: 30px;
  }
  .contact__role {
    font-size: 15.5px;
    font-weight: 400;
    line-height: 22px;
  }
  .contact__list {
    list-style: none;
    margin-top: 20px;
  }
  .contact__item {
    display: flex;
    align-items: center;
    font-size: 15.5px;
    line-height: 26px;
  }
  .contact__icon {
    width: 13px;
    height: 13px;
    margin: 0 18px 0 0;
    flex: none;
  }
  .contact__address {
    margin-top: 6px;
    font-size: 15.5px;
    line-height: 25px;
  }
</style>
</head>
<body>
<main class="canvas">
  <section class="card card--front">
    <p class="front__name">K T Masonry</p>
    <p class="front__web">www.ktmasonry.com</p>
  </section>

  <section class="card card--back">
    <div class="brand">
      <span class="brand__square"></span>
      <span class="brand__name">K T Masonry</span>
    </div>

    <div class="contact">
      <h1 class="contact__name">Daniel Harper</h1>
      <p class="contact__role">Managing Director</p>
      <ul class="contact__list">
        <li class="contact__item">
          <svg class="contact__icon" viewBox="0 0 16 16" aria-hidden="true">
            <path fill="#163a5c" d="M2 5c0-2 3-3 6-3s6 1 6 3v1h-3V5H5v1H2z M3 8l2-2h6l2 2v6H3z"/>
            <circle cx="8" cy="10.5" r="1.8" fill="#e4e4e4"/>
          </svg>
          000 0000 0000
        </li>
        <li class="contact__item">
          <svg class="contact__icon" viewBox="0 0 16 16" aria-hidden="true">
            <rect x="1" y="3" width="14" height="10" fill="#163a5c"/>
            <path d="M1 3l7 6 7-6" fill="none" stroke="#e4e4e4" stroke-width="1.3"/>
          </svg>
          daniel@ktmasonry.com
        </li>
        <li class="contact__item">
          <svg class="contact__icon" viewBox="0 0 16 16" aria-hidden="true">
            <circle cx="8" cy="8" r="6.5" fill="none" stroke="#163a5c" stroke-width="1.5"/>
            <ellipse cx="8" cy="8" rx="2.8" ry="6.5" fill="none" stroke="#163a5c" stroke-width="1.2"/>
            <path d="M1.5 8h13M2.5 5h11M2.5 11h11" stroke="#163a5c" stroke-width="1"/>
          </svg>
          www.ktmasonry.com
        </li>
      </ul>
      <p class="contact__address">18 Harbour Rd., Point Cruz,<br>Honiara, SB 00100</p>
    </div>
  </section>
</main>
</body>
</html>
```